Brightmoor - a website to encourage people to spend time in nature

I have a squarespace site with some content on it but the squarespace template doesn't completely suit my needs, I keep fiddling with the template but actually I need some professional help to get it looking the way I want and with the right 'mood'.
The website is for "Brightmoor" - it will be a blog where I write about the importance of nature for good health. I also want to use the website to market services such as outdoor coaching, retreats and walking workshops.
This has been in my head for a LONG time and I currently only use instagram for micro-blogs but it's time for me to get this moving. I've previously engaged other designers on branding for it but they just didn't get it quite the way that I wanted it and I wasn't completely happy with the results. It's been a process for me as to what I want but in the meantime I just didn't come back to the design aspect of it now. I'm looking for a designer who understands the purpose of the website, the ethos and can help me realise this into a design that's clean, clear and simple.

Please note that I have a domain (brightmoor.org) and a lot of content drafted on squarespace already. I have published it with password protection - password is brightmoor2020 - it still has some of the original template on it, but does have some content. Don't take it as anything to follow in particular, i am looking for fresh eyes and fresh ideas.

Target Market(s)

There are three main groups that I want to target - people who are suffering from stress and anxiety, people who treat them and parents who want to get their kids outside (thereby preventing stress and anxiety)

Contact Information for Business Card

Joan Petrie
Brightmoor
Telephone +44 7700 900417
brightmoor@mailvane.com

Logo Text

Brightmoor - if that. I have an idea that the logo should have a leaf on it somewhere, or maybe just be a leaf.

Coding

Coded - Design and coding required

Number of Pages Required

5+ page

Font styles to use
Serif
Sans Serif

Colors
add136
33b8a4
34a6d7
3377b5

Requirements
Must have
• Space for lots of images. The ability for me to edit the pages if I need to. Be user friendly. Look beautiful.
• For an idea of the images I use and the content I'm interested in writing about have a look at @brightmoor on instagram.
• That pop up about cookies so I am complying with data laws.
Should not have
• Must not be too 'busy' I'd like to avoid too much movement.

```html
<!DOCTYPE html>
<html lang="en">
<head>
<meta charset="utf-8">
<title>Brightmoor – Home and Cookie Notice</title>
<link href="https://fonts.googleapis.com/css2?family=EB+Garamond:ital,wght@0,500;1,400&family=Montserrat:wght@700&family=Poppins:wght@400;500;600&display=swap" rel="stylesheet">
<style>
  :root {
    --lime: #add136;
    --sky: #34a6d7;
    --navy: #3377b5;
    --ink: #1f2a2a;
    --text: #333;
    --paper: #ffffff;
    --backdrop: #ffffff;
    --shade: rgba(20, 20, 20, 0.72);
    --line: #dcdcdc;
    --icon-bg: #ececec;
  }
  * { box-sizing: border-box; margin: 0; padding: 0; }
  html, body { width: 940px; height: 1200px; overflow: hidden; background: var(--backdrop); }
  .stage { position: relative; width: 1700px; height: 2180px; transform: scale(0.552941); transform-origin: 0 0; }

  .page { position: absolute; top: 78px; width: 775px; height: 2025px; background: var(--paper); overflow: hidden;
          font-family: "Poppins", sans-serif; color: var(--text); box-shadow: 0 0 6px rgba(0,0,0,.12); }
  .page--home { left: 67px; }
  .page--cookies { left: 868px; }
  .page > * { position: absolute; }

  .menu-toggle { left: 72px; top: 44px; width: 22px; height: 16px; border-top: 2px solid var(--ink); border-bottom: 2px solid var(--ink); }
  .menu-toggle::after { content: ""; position: absolute; left: 0; right: 0; top: 5px; border-top: 2px solid var(--ink); }

  .brand { left: 0; right: 0; top: 18px; text-align: center; }
  .brand__mark { display: block; width: 44px; height: 44px; margin: 0 auto 12px; border-radius: 50%; background: var(--lime); }
  .brand__name { font-family: "EB Garamond", serif; font-weight: 500; font-size: 30px; color: var(--navy); }

  .social { right: 78px; top: 37px; display: flex; gap: 4px; }
  .social__item { width: 28px; height: 28px; border-radius: 50%; background: var(--icon-bg); display: flex; align-items: center; justify-content: center; }

  .tagline { left: 0; right: 0; top: 140px; text-align: center; font-family: "EB Garamond", serif; font-style: italic; font-size: 28px; color: var(--ink); }

  .hero { left: 72px; top: 191px; width: 630px; height: 361px;
          background: linear-gradient(180deg, #b9bdb4 0%, #6d7a55 35%, #3f5a24 65%, #6f8f2e 85%, #4c6a1f 100%);
          display: flex; align-items: center; justify-content: center; }
  .hero__title { font-family: "Montserrat", sans-serif; font-weight: 700; font-size: 40px; color: #fff; letter-spacing: 1px; margin-top: 92px; }

  .intro { left: 72px; top: 585px; width: 410px; font-size: 11px; line-height: 17px; }
  .btn { display: inline-block; border-radius: 20px; font-family: "Poppins", sans-serif; font-weight: 500; text-align: center; }
  .btn--consult { left: 504px; top: 597px; width: 197px; height: 38px; line-height: 38px; background: var(--lime); color: #fff; font-size: 10.5px; }

  .service { top: 714px; width: 192px; }
  .service__title { font-size: 16px; font-weight: 500; color: var(--sky); margin-bottom: 9px; }
  .service__text { font-size: 8.6px; line-height: 13.8px; text-align: justify; color: var(--ink); }
  .service__link { display: inline-block; margin-top: 12px; font-size: 10px; color: var(--ink); border-bottom: 1px solid var(--ink); line-height: 12px; }

  .photo { display: block; }
  .photo--walk { left: 265px; top: 909px; width: 436px; height: 291px;
                 background: linear-gradient(180deg, #dcdcdf 0%, #c7c8c6 30%, #5a4a38 42%, #6b3a2c 55%, #55603a 70%, #5d5446 100%); }
  .photo--sea { left: 72px; top: 1454px; width: 436px; height: 291px;
                background: linear-gradient(180deg, #4d6c9a 0%, #7890b0 45%, #a5a9b8 65%, #28406a 70%, #172c52 100%); }

  .feature { width: 248px; height: 227px; padding: 28px 14px 0; color: #fff; }
  .feature--stress { left: 72px; top: 941px; background: var(--lime); }
  .feature--health { left: 454px; top: 1486px; background: var(--sky); }
  .feature__title { font-family: "Montserrat", sans-serif; font-weight: 700; font-size: 19px; }
  .feature__rule { width: 58px; border-top: 2px solid #fff; margin: 14px 0 14px; }
  .feature__text { font-size: 8.6px; line-height: 17px; text-align: justify; }
  .feature .btn { margin-top: 12px; background: #fff; font-size: 10px; padding: 0 13px; height: 31px; line-height: 31px; }
  .feature--stress .btn { color: var(--lime); }
  .feature--health .btn { color: var(--navy); }

  .quote { left: 0; right: 0; top: 1252px; text-align: center; font-family: "EB Garamond", serif; font-style: italic; color: var(--ink); }
  .quote__text { font-size: 24px; line-height: 35px; }
  .quote__cite { display: block; margin-top: 18px; font-size: 13px; }

  .closing { left: 0; right: 0; top: 1806px; text-align: center; font-family: "EB Garamond", serif; font-style: italic; font-size: 27px; line-height: 35px; color: var(--ink); }
  .btn--talk { left: 340px; top: 1893px; width: 94px; height: 31px; line-height: 31px; background: var(--lime); color: #fff; font-size: 10px; }

  .footer-rule { left: 72px; right: 72px; top: 1967px; border-top: 1px solid var(--line); }
  .footer { left: 0; right: 0; top: 1989px; text-align: center; font-size: 10px; color: var(--ink); }

  .shade { inset: 0; background: var(--shade); }
  .cookie { left: 197px; top: 147px; width: 380px; height: 197px; background: var(--lime); border: 3px solid #fff; text-align: center; color: #fff; padding: 42px 28px 0; }
  .cookie__close { position: absolute; right: 10px; top: 10px; width: 18px; height: 18px; border-radius: 50%; background: #4a5a1c; color: #fff; font-size: 12px; line-height: 17px; }
  .cookie__title { font-size: 13px; font-weight: 600; margin-bottom: 14px; }
  .cookie__text { font-size: 8.4px; line-height: 15px; }
  .cookie .btn { margin-top: 16px; background: #fff; color: var(--lime); font-size: 10.5px; width: 70px; height: 24px; line-height: 24px; }
</style>
</head>
<body>
<div class="stage">

  <!-- Home page -->
  <section class="page page--home">
    <span class="menu-toggle"></span>
    <div class="brand"><span class="brand__mark"></span><span class="brand__name">Brightmoor</span></div>
    <div class="social">
      <span class="social__item"></span><span class="social__item"></span><span class="social__item"></span>
      <span class="social__item"><svg width="12" height="12" viewBox="0 0 12 12"><circle cx="5" cy="5" r="3.2" fill="none" stroke="#1f2a2a" stroke-width="1.5"/><line x1="7.4" y1="7.4" x2="10.5" y2="10.5" stroke="#1f2a2a" stroke-width="1.6"/></svg></span>
    </div>
    <p class="tagline">We encourage people to spend time in nature</p>
    <div class="hero" role="img" aria-label="Sunlit path through a pine forest"><h1 class="hero__title">BRIGHTMOOR</h1></div>
    <p class="intro">Our aim is to help people connect with nature as a means to feeling better. We do this in a number of ways. Find out more below. Start 'em young. Children have an intuitive connection with nature. Watch a young child in a garden and you'll spot the fascination they have.</p>
    <a class="btn btn--consult">SCHEDULE A FREE CONSULTATION</a>

    <div class="service" style="left:72px"><h2 class="service__title">Our Services</h2><p class="service__text">Brightmoor Walking is an initiative aimed at getting people back into nature in the most gentlest of ways - by taking a walk with friends in the great outdoors. The concept is simple.</p><a class="service__link">See All Services »</a></div>
    <div class="service" style="left:292px"><h2 class="service__title">Outdoor Coaching</h2><p class="service__text">Only one thing better than coaching and that's coaching in the great outdoors. We believe that being out in nature gives you a greater sense of perspective when working through issues.</p><a class="service__link">See All Services »</a></div>
    <div class="service" style="left:512px"><h2 class="service__title">Retreats And Walking</h2><p class="service__text">Sometimes you just need to get away from it all. And that's where Brightmoor retreats come in. Our retreats are based at Heathway Cottage located at the foot of the Carrow Fell.</p><a class="service__link">See All Services »</a></div>

    <div class="photo photo--walk" role="img" aria-label="Walker on a wooden boardwalk across moorland"></div>
    <div class="feature feature--stress"><h2 class="feature__title">STRESS AND ANXIETY</h2><div class="feature__rule"></div><p class="feature__text">Only one thing better than coaching and that's coaching in the great outdoors. We believe that being out in nature gives you a greater sense of perspective when working through issues.</p><a class="btn">READ MORE</a></div>

    <blockquote class="quote"><p class="quote__text">Nam libero tempore, cum soluta nobis est eligendi optio<br>cumque nihil impedit quo minus id quod maxime<br>placeat facere possimus</p><cite class="quote__cite">— Blandit Lectus</cite></blockquote>

    <div class="photo photo--sea" role="img" aria-label="Dark sea under an evening sky"></div>
    <div class="feature feature--health"><h2 class="feature__title">GOOD HEALTH</h2><div class="feature__rule"></div><p class="feature__text">Our retreats are designed to deepen your connection to nature, to remind you that you are a part of nature and not apart from it. By doing this, you get a chance to reset.</p><a class="btn">READ MORE</a></div>

    <p class="closing">Let's talk!<br>Your first consultation is free.</p>
    <a class="btn btn--talk">READ MORE</a>
    <div class="footer-rule"></div>
    <p class="footer">Copyrights @ 2020 Brightmoor. All Rights Reserved.</p>
  </section>

  <!-- Home page with cookie notice -->
  <section class="page page--cookies">
    <span class="menu-toggle"></span>
    <div class="brand"><span class="brand__mark"></span><span class="brand__name">Brightmoor</span></div>
    <div class="social">
      <span class="social__item"></span><span class="social__item"></span><span class="social__item"></span>
      <span class="social__item"><svg width="12" height="12" viewBox="0 0 12 12"><circle cx="5" cy="5" r="3.2" fill="none" stroke="#1f2a2a" stroke-width="1.5"/><line x1="7.4" y1="7.4" x2="10.5" y2="10.5" stroke="#1f2a2a" stroke-width="1.6"/></svg></span>
    </div>
    <p class="tagline">We encourage people to spend time in nature</p>
    <div class="hero" role="img" aria-label="Sunlit path through a pine forest"><h1 class="hero__title">BRIGHTMOOR</h1></div>
    <p class="intro">Our aim is to help people connect with nature as a means to feeling better. We do this in a number of ways. Find out more below. Start 'em young. Children have an intuitive connection with nature. Watch a young child in a garden and you'll spot the fascination they have.</p>
    <a class="btn btn--consult">SCHEDULE A FREE CONSULTATION</a>

    <div class="service" style="left:72px"><h2 class="service__title">Our Services</h2><p class="service__text">Brightmoor Walking is an initiative aimed at getting people back into nature in the most gentlest of ways - by taking a walk with friends in the great outdoors. The concept is simple.</p><a class="service__link">See All Services »</a></div>
    <div class="service" style="left:292px"><h2 class="service__title">Outdoor Coaching</h2><p class="service__text">Only one thing better than coaching and that's coaching in the great outdoors. We believe that being out in nature gives you a greater sense of perspective when working through issues.</p><a class="service__link">See All Services »</a></div>
    <div class="service" style="left:512px"><h2 class="service__title">Retreats And Walking</h2><p class="service__text">Sometimes you just need to get away from it all. And that's where Brightmoor retreats come in. Our retreats are based at Heathway Cottage located at the foot of the Carrow Fell.</p><a class="service__link">See All Services »</a></div>

    <div class="photo photo--walk" role="img" aria-label="Walker on a wooden boardwalk across moorland"></div>
    <div class="feature feature--stress"><h2 class="feature__title">STRESS AND ANXIETY</h2><div class="feature__rule"></div><p class="feature__text">Only one thing better than coaching and that's coaching in the great outdoors. We believe that being out in nature gives you a greater sense of perspective when working through issues.</p><a class="btn">READ MORE</a></div>

    <blockquote class="quote"><p class="quote__text">Nam libero tempore, cum soluta nobis est eligendi optio<br>cumque nihil impedit quo minus id quod maxime<br>placeat facere possimus</p><cite class="quote__cite">— Blandit Lectus</cite></blockquote>

    <div class="photo photo--sea" role="img" aria-label="Dark sea under an evening sky"></div>
    <div class="feature feature--health"><h2 class="feature__title">GOOD HEALTH</h2><div class="feature__rule"></div><p class="feature__text">Our retreats are designed to deepen your connection to nature, to remind you that you are a part of nature and not apart from it. By doing this, you get a chance to reset.</p><a class="btn">READ MORE</a></div>

    <p class="closing">Let's talk!<br>Your first consultation is free.</p>
    <a class="btn btn--talk">READ MORE</a>
    <div class="footer-rule"></div>
    <p class="footer">Copyrights @ 2020 Brightmoor. All Rights Reserved.</p>

    <div class="shade"></div>
    <div class="cookie" role="dialog" aria-label="Cookie notice">
      <span class="cookie__close">×</span>
      <h2 class="cookie__title">This Website Uses Cookies:</h2>
      <p class="cookie__text">Nemo enim ipsam voluptatem quia voluptas sit aspernatur aut odit aut fugit, sed quia consequuntur magni dolores eos qui ratione voluptatem sequi nesciunt.</p>
      <a class="btn">Accept</a>
    </div>
  </section>

</div>
</body>
</html>
```